Design for iOS app - Scanner App

We are developing an iOS app that is scanning receipts and mailing them to a predefined email address. The app should work more or less like TallySnap app (a short demo of the TallySnap app is available here: https://www.vidplume.example/watch?v=QmR7tkLpZwA).

We have prototyped the app in the link below:
http://app.draftloom.example/view/a71c3d9f8820b15ce47d0a6e2f9b14c3

NB!: Please do not follow the mockups literally, but the iOS Human Interface Guidelines!

The technical specifications and descriptions of the app's functionalities are available in the link below:
https://files.norvapage.example/document/d/9xWpa-QL3bRnTyVMhKeZ7-uFd_2Hsqtw4c8PjKmo1/edit?usp=sharing

Requirements for the design:

- The design should be provided as PSD, where each page/section should be in its own PSD file OR all pages/sections should be represented as folder groups in a single PSD file.

- All graphical elements in the design should be delivered as single layers which can then be extracted from the PSD.

- All graphical elements (icons, graphical buttons, etc.) should be provided as vector objects in the PSD, so that they can be exported into different sizes without loss of quality (for responsiveness).

- The design should use either web safe fonts or Varlo Typefaces.

Instructions for the design:

The design should have habitual user interface like ordinary iOS navigation stack, with navigation bar on the top and all other elements on the bottom. That means just to make the top bar in your app be more like iOS. Please follow the iOS Human Interface Guidelines, not the mockups literally .
FX: the e small elements in Dimensions screen like delete icons and active checkbox. In
https://devhub.quintora.example/library/ios/documentation/UserExperience/Conceptual/MobileHIG/LayoutandAppearance.html#//quin_ref/doc/uid/TP50017829-CH31-SW1
is described that interface elements should be at least 44x44 px - it's normal practice for all mobile development (iOS, android), so you should consider this too.

Please also provide an app icon and suggest a logo for the app.

Requirements
Must have
• Please make sure that the design is flat. Like iOS app, Pagefold, Varlo apps etc.
Nice to have
• The design could be somewhat like the design for Brightwick Pagefold(https://apps.quintora.example/bg/app/brightwick-pagefold/id472915630?mt=8) without being too similar
Should not have
• 3D look

```html
<!DOCTYPE html>
<html lang="en">
<head>
<meta charset="utf-8">
<title>KLIPO — Presentation Apps</title>
<link rel="stylesheet" href="https://fonts.googleapis.com/css2?family=Exo+2:wght@400;500;600;700;800;900&display=swap">
<style>
  :root {
    --brand-red: #e44c3c;
    --brand-red-dark: #c9382b;
    --strip-red: #d2685c;
    --white: #ffffff;
    --panel-light: #e9ecef;
    --panel-grey-top: #5d6268;
    --panel-grey-bottom: #a4a8ad;
    --row-bg: #eeeeee;
    --field-bg: #e2e2e2;
    --text-dark: #3a3a3a;
    --text-muted: #8a8a8a;
    --accent-blue: #4fc3f7;
    --accent-blue-dark: #36a9dc;
    --accent-green: #1abc9c;
    --delete-red: #e44c3c;
  }
  * { box-sizing: border-box; margin: 0; padding: 0; }
  html, body { width: 1200px; height: 1055px; overflow: hidden; }
  body { font-family: "Exo 2", sans-serif; background: var(--brand-red); color: var(--white); position: relative; }

  .header-band { position: absolute; left: 0; top: 0; width: 1200px; height: 170px; background: var(--brand-red); }
  .brand-wordmark { position: absolute; left: 82px; top: 46px; font-size: 74px; font-weight: 900; letter-spacing: -2px; line-height: 1; color: var(--white); }
  .presentation-title { position: absolute; right: 60px; top: 58px; font-size: 32px; font-weight: 700; letter-spacing: 0.5px; line-height: 1; }

  .accent-strip { position: absolute; left: 0; top: 170px; width: 1200px; height: 14px; background: var(--strip-red); }

  .showcase { position: absolute; top: 184px; left: 0; width: 1200px; height: 689px; display: flex; }
  .panel-detail { width: 612px; height: 100%; background: var(--panel-light); position: relative; overflow: hidden; }
  .panel-splash { width: 588px; height: 100%; background: linear-gradient(160deg, var(--panel-grey-top), var(--panel-grey-bottom)); position: relative; overflow: hidden; }

  /* Dimensions screen */
  .screen-dimensions { position: absolute; left: 96px; top: 36px; width: 420px; height: 700px; background: var(--white); border-radius: 6px 6px 0 0; overflow: hidden; box-shadow: 0 2px 14px rgba(0,0,0,0.12); }
  .nav-bar { height: 78px; background: var(--brand-red); display: flex; align-items: center; justify-content: center; position: relative; }
  .nav-back { position: absolute; left: 16px; top: 27px; }
  .nav-title { font-size: 38px; font-weight: 900; letter-spacing: -1px; color: var(--white); }
  .section-head { height: 52px; background: var(--row-bg); display: flex; align-items: center; padding: 0 16px; color: var(--text-dark); font-weight: 700; font-size: 20px; gap: 10px; }
  .section-head .spacer { flex: 1; }
  .active-toggle { display: flex; align-items: center; gap: 10px; font-weight: 700; font-size: 19px; color: var(--text-dark); }
  .check-box { width: 44px; height: 32px; background: var(--accent-blue); display: flex; align-items: center; justify-content: center; }
  .dimension { padding: 14px 16px 0; position: relative; color: var(--text-dark); }
  .dimension-name { font-size: 20px; font-weight: 700; display: flex; align-items: center; gap: 8px; }
  .dimension-values { font-size: 17px; color: var(--text-muted); line-height: 1.25; margin-top: 4px; }
  .dimension-actions { position: absolute; right: 0; top: 0; display: flex; flex-direction: column; align-items: flex-end; gap: 10px; }
  .add-button { width: 100px; height: 40px; background: var(--accent-blue); color: var(--white); font-weight: 700; font-size: 15px; display: flex; align-items: center; justify-content: center; border-bottom: 4px solid var(--accent-blue-dark); }
  .active-toggle.row { padding-right: 16px; }
  .value-field { margin: 12px 0 0; height: 56px; background: var(--field-bg); width: 100%; }
  .action-button { margin: 16px 16px 0; height: 64px; display: flex; align-items: center; justify-content: center; color: var(--white); font-size: 24px; font-weight: 500; }
  .action-button.save { background: var(--accent-blue); border-bottom: 5px solid var(--accent-blue-dark); }
  .action-button.cancel { background: var(--accent-green); }

  /* Splash screen */
  .screen-splash { position: absolute; left: 154px; top: 86px; width: 300px; height: 520px; background: linear-gradient(170deg, var(--brand-red), var(--brand-red-dark)); border-radius: 6px; display: flex; flex-direction: column; align-items: center; justify-content: center; gap: 10px; box-shadow: 0 4px 20px rgba(0,0,0,0.25); }
  .status-bar { position: absolute; top: 0; left: 0; right: 0; height: 18px; background: rgba(0,0,0,0.85); border-radius: 6px 6px 0 0; font-size: 11px; display: flex; align-items: center; justify-content: center; }
  .splash-mark { width: 14px; height: 14px; background: var(--white); }
  .splash-name { font-size: 40px; font-weight: 900; letter-spacing: -1px; line-height: 1; }
  .splash-tagline { font-size: 10px; letter-spacing: 1px; opacity: 0.85; }
  .callout { position: absolute; left: 28px; top: 432px; display: flex; align-items: center; }
  .callout-label { font-size: 16px; line-height: 1.05; color: var(--white); font-weight: 500; }
  .callout-line { width: 268px; height: 1px; background: var(--white); margin-left: 8px; }
  .callout-dot { width: 8px; height: 8px; border-radius: 50%; background: var(--white); }

  .footer-band { position: absolute; left: 0; top: 873px; width: 1200px; height: 182px; display: flex; align-items: center; justify-content: center; }
  .footer-note { font-size: 24px; font-weight: 400; letter-spacing: 0.6px; }
</style>
</head>
<body>
  <header class="header-band">
    <div class="brand-wordmark">KLIPO</div>
    <div class="presentation-title">PRESENTATION APPS</div>
  </header>
  <div class="accent-strip"></div>

  <main class="showcase">
    <section class="panel-detail">
      <div class="screen-dimensions">
        <div class="nav-bar">
          <svg class="nav-back" width="16" height="24" viewBox="0 0 16 24"><path d="M13 2 L3 12 L13 22" fill="none" stroke="#fff" stroke-width="3"/></svg>
          <span class="nav-title">KLIPO</span>
        </div>
        <div class="section-head">
          <svg width="20" height="16" viewBox="0 0 20 16"><rect y="0" width="20" height="3" fill="#3a3a3a"/><rect y="6.5" width="20" height="3" fill="#3a3a3a"/><rect y="13" width="20" height="3" fill="#3a3a3a"/></svg>
          <span>Dimensions</span>
          <span class="spacer"></span>
          <span class="active-toggle">Active
            <span class="check-box"><svg width="20" height="14" viewBox="0 0 20 14"><path d="M2 7 L8 12 L18 2" fill="none" stroke="#fff" stroke-width="3"/></svg></span>
          </span>
        </div>

        <div class="dimension">
          <div class="dimension-name">Daily cost
            <svg width="12" height="14" viewBox="0 0 12 14"><rect x="1" y="3" width="10" height="11" rx="1" fill="#e44c3c"/><rect x="0" y="0" width="12" height="2" fill="#e44c3c"/></svg>
          </div>
          <div class="dimension-values">Drink<br>Snack<br>Transport</div>
          <div class="dimension-actions">
            <div class="add-button">ADD</div>
            <span class="active-toggle row">Active
              <span class="check-box"><svg width="20" height="14" viewBox="0 0 20 14"><path d="M2 7 L8 12 L18 2" fill="none" stroke="#fff" stroke-width="3"/></svg></span>
            </span>
          </div>
          <div class="value-field"></div>
        </div>

        <div class="dimension">
          <div class="dimension-name">Bill
            <svg width="12" height="14" viewBox="0 0 12 14"><rect x="1" y="3" width="10" height="11" rx="1" fill="#e44c3c"/><rect x="0" y="0" width="12" height="2" fill="#e44c3c"/></svg>
          </div>
          <div class="dimension-values">Credit Card</div>
          <div class="dimension-actions">
            <div class="add-button">ADD</div>
          </div>
          <div class="value-field"></div>
        </div>

        <div class="dimension">
          <div class="dimension-name">Dimension 3
            <svg width="12" height="14" viewBox="0 0 12 14"><rect x="1" y="3" width="10" height="11" rx="1" fill="#e44c3c"/><rect x="0" y="0" width="12" height="2" fill="#e44c3c"/></svg>
          </div>
        </div>

        <div class="action-button save">Save</div>
        <div class="action-button cancel">Cancel</div>
      </div>
    </section>

    <section class="panel-splash">
      <div class="screen-splash">
        <div class="status-bar">10:38</div>
        <div class="splash-mark"></div>
        <div class="splash-name">KLIPO</div>
        <div class="splash-tagline">SCAN YOUR RECEIPTS</div>
      </div>
      <div class="callout">
        <div class="callout-label">SPLASH<br>SCREEN</div>
        <div class="callout-line"></div>
        <div class="callout-dot"></div>
      </div>
    </section>
  </main>

  <footer class="footer-band">
    <p class="footer-note">PLEASE, FOLLOW THE LINKS FOR DETAILED PRESENTATION</p>
  </footer>
</body>
</html>
```